Art Business Needs a Wordpress Theme

I need a Wordpress theme for my company, Pim Pim Nook. Pim Pim stands for Love, Local and the company's focus is to increase awareness of local art and artists. The site will have a blog with posts that showcase local art, art how-to techniques, featured artists and art events. These could be broken down into separate pages or just kept within the homepage. I have a logo that I would like to incorporate. The only request I will make about the layout is that it can feature pictures prominently. Eventually with the help of a Fundmoor campaign I would like to turn the site into an upscale e-commerce platform for member artists of the site. The blog that you are designing will be built on as the business grows into its full vision.

Target Market(s)

Young professionals, Art fans and home designers

Industry/Entity Type

Business

Number of Pages Required

3 page

Font styles to use
Sans Serif

Colors
eda3c7
e667a6
e34197
f59195
f04a50
f68d4d
f37122

Requirements
Must have
• An about page and a contact page. I would like it if the logo was featured on the top left of the screen along with the words Love. Local. Art.
Nice to have
• Perhaps if possible it would be cool to have a way for people to enter their email if they were interested in joining a mailing list or having the Social media information displayed on a sidebar.

```html
<!DOCTYPE html>
<html lang="en">
<head>
<meta charset="utf-8">
<title>Pim Pim Nook — Love. Local. Art.</title>
<link href="https://fonts.googleapis.com/css2?family=Open+Sans:wght@400;600;700&display=swap" rel="stylesheet">
<style>
:root{
  --page:#ebe4d2;
  --card:#fbf4e2;
  --card-edge:#e6dcc2;
  --header:#fffaf0;
  --nav:#4a4a4a;
  --pink:#e34197;
  --pink-soft:#eda3c7;
  --pink-mid:#e667a6;
  --orange:#f37122;
  --orange-soft:#f68d4d;
  --coral:#f04a50;
  --text:#6b6258;
  --title:#4a433b;
  --bar:#e9e3d6;
  --white:#ffffff;
}
*{box-sizing:border-box;margin:0;padding:0}
html,body{width:1200px;height:2440px;overflow:hidden}
body{background:var(--page);font-family:"Open Sans",Arial,sans-serif;color:var(--text);position:relative}
.card{position:absolute;left:60px;top:20px;width:1070px;height:2320px;background:var(--card);border:1px solid var(--card-edge);border-radius:18px;box-shadow:0 6px 24px rgba(120,100,60,.18)}
.header{position:absolute;left:60px;top:20px;width:1070px;height:200px;background:var(--header);border-radius:18px 18px 0 0}
.logo{position:absolute;left:130px;top:50px;display:flex;flex-direction:column;align-items:center;gap:8px}
.logo-mark{width:90px;height:90px;border-radius:50%;background:var(--pink-soft)}
.logo-name{font-size:17px;font-weight:600;color:var(--pink)}
.tagline{position:absolute;left:250px;top:92px;font-size:14px;color:var(--pink-mid);font-weight:600;letter-spacing:1px}
.nav{position:absolute;left:560px;top:150px;height:36px;width:520px;background:var(--nav);border-radius:18px;display:flex;align-items:center;justify-content:space-around;padding:0 10px}
.nav a{color:var(--white);text-decoration:none;font-size:12px;padding:6px 12px;border-radius:14px}
.nav a.active{background:var(--pink)}
.hero{position:absolute;left:60px;top:220px;width:1070px;height:400px;background:linear-gradient(100deg,#7a8d8c 0%,#c9b9a2 30%,#e9e4dc 55%,#b9c3c2 80%,#e28a5a 100%)}
.hero-caption{position:absolute;left:500px;top:520px;width:630px;height:56px;background:rgba(40,40,40,.55);color:var(--white);font-size:20px;display:flex;align-items:center;padding-left:24px}
.posts{position:absolute;left:120px;top:690px;width:760px}
.post{height:470px;margin-bottom:20px;position:relative}
.post-title{height:40px;background:var(--bar);display:flex;align-items:center;justify-content:space-between;padding:0 12px;font-size:14px;font-weight:700;color:var(--title)}
.post-title i{width:22px;height:22px;background:#c9c2b4;display:block}
.meta{display:flex;gap:26px;font-size:10px;margin:10px 0 12px;color:#8a8176}
.meta span::before{content:"";display:inline-block;width:8px;height:8px;background:#b7ae9f;margin-right:5px;border-radius:2px}
.post-body{display:flex;gap:20px}
.thumb{width:240px;height:210px;flex:none}
.post-body p{font-size:11px;line-height:17px}
.post-foot{font-size:11px;line-height:17px;margin-top:14px}
.btn{display:inline-block;margin-top:16px;background:var(--orange);color:var(--white);font-size:10px;font-weight:700;padding:7px 14px;border-radius:3px}
.sidebar{position:absolute;left:890px;top:690px;width:190px}
.widget{margin-bottom:18px;background:var(--white);border:1px solid var(--card-edge)}
.widget h3{background:var(--orange);color:var(--white);font-size:12px;font-weight:700;padding:10px 12px;letter-spacing:.5px}
.signup{background:var(--pink);padding:16px 14px;text-align:center;color:var(--white);border:none}
.signup h4{font-size:13px;font-weight:700;line-height:18px;margin-bottom:14px}
.signup .field{background:var(--white);color:#999;font-size:10px;text-align:left;padding:6px 8px;margin-bottom:8px}
.signup .submit{display:inline-block;background:#7a2a55;font-size:10px;padding:6px 16px;margin-top:4px}
.cats li{list-style:none;font-size:10px;padding:14px 12px;border-bottom:1px solid #eee}
.pop{display:flex;gap:8px;padding:10px;border-bottom:1px solid #eee}
.pop div{width:54px;height:40px;flex:none}
.pop p{font-size:9px;line-height:13px}
.flickr{display:grid;grid-template-columns:repeat(3,1fr);gap:6px;padding:10px}
.flickr div{height:52px}
.tweet{display:flex;gap:8px;padding:10px;font-size:9px;line-height:13px}
.tweet i{width:14px;height:14px;background:var(--orange-soft);border-radius:50%;flex:none}
.tweet b{color:var(--pink)}
.footer-nav{position:absolute;left:60px;top:2240px;width:1070px;display:flex;justify-content:center;gap:48px;font-size:11px;color:var(--title)}
.footer-bar{position:absolute;left:60px;top:2285px;width:1070px;height:40px;border-top:1px solid var(--card-edge);display:flex;align-items:center;justify-content:space-between;padding:0 40px;font-size:9px}
.social{display:flex;gap:8px}
.social i{width:14px;height:14px;border-radius:50%;background:#6d655a;display:block}
</style>
</head>
<body>
<div class="card"></div>
<header class="header"></header>
<div class="logo"><div class="logo-mark"></div><span class="logo-name">Pim Pim Nook</span></div>
<nav class="nav"><a class="active">Home</a><a>About Us</a><a>Gallery</a><a>Latest Blog</a><a>Testimonials</a><a>Contact Us</a></nav>

<div class="hero" role="img" aria-label="Photo of a smiling painter working at an easel in a bright studio"></div>
<div class="hero-caption">Sed laoreet dui eu augue lobortis, nec pulvinar neque</div>

<main class="posts">
  <article class="post">
    <div class="post-title">LOREM IPSUM DOLOR SIT AMET, CONSECTETUR ADIPISCING ELIT<i></i></div>
    <div class="meta"><span>14.06.2013</span><span>By Admin</span><span>0 Comments</span><span>Portfolio</span></div>
    <div class="post-body">
      <div class="thumb" role="img" aria-label="Paintbrush mixing blue and white paint on a canvas" style="background:linear-gradient(135deg,#d9e2ea,#5f7fa4 60%,#c9a27a)"></div>
      <p>Interdum et malesuada fames ac ante ipsum primis in faucibus. Vivamus eget neque tempor vulputate nunc vitae sagittis. Quisque scelerisque mi quis nibh porta mattis sed eu velit. Nunc feugiat erat sed velit luctus, et pretium orci dictum. Donec commodo purus vel lectus gravida, vitae tincidunt massa luctus. Aliquam erat volutpat. Sed gravida augue non porta ultrices. Curabitur in lacus et odio vestibulum semper. Praesent quis arcu et neque porttitor varius sit amet eu enim. Mauris sed mauris ut nibh lacinia pulvinar. Nam ut lorem vel sapien dictum blandit. Integer vitae tortor a nisl cursus faucibus ac nec erat. Vestibulum ante ipsum primis in faucibus orci luctus et ultrices posuere cubilia curae.</p>
    </div>
    <p class="post-foot">Sed tristique purus vel augue dapibus, quis fringilla lorem bibendum. Etiam vitae ligula nec urna suscipit faucibus. Nullam vel dui ac tellus vestibulum tempor eget in mauris. Cras fermentum odio a quam pretium, eget placerat nisi venenatis. Phasellus ac nunc porta, interdum magna at, varius enim.</p>
    <span class="btn">READ MORE</span>
  </article>

  <article class="post">
    <div class="post-title">LOREM IPSUM DOLOR SIT AMET, CONSECTETUR ADIPISCING ELIT<i></i></div>
    <div class="meta"><span>14.06.2013</span><span>By Admin</span><span>0 Comments</span><span>Portfolio</span></div>
    <div class="post-body">
      <div class="thumb" role="img" aria-label="Artist beside a colourful splashed painting" style="background:linear-gradient(135deg,#4a3a5a,#d94f6a 45%,#f2c14a 70%,#6aa0d8)"></div>
      <p>Interdum et malesuada fames ac ante ipsum primis in faucibus. Vivamus eget neque tempor vulputate nunc vitae sagittis. Quisque scelerisque mi quis nibh porta mattis sed eu velit. Nunc feugiat erat sed velit luctus, et pretium orci dictum. Donec commodo purus vel lectus gravida, vitae tincidunt massa luctus. Aliquam erat volutpat. Sed gravida augue non porta ultrices. Curabitur in lacus et odio vestibulum semper. Praesent quis arcu et neque porttitor varius sit amet eu enim. Mauris sed mauris ut nibh lacinia pulvinar. Nam ut lorem vel sapien dictum blandit. Integer vitae tortor a nisl cursus faucibus ac nec erat. Vestibulum ante ipsum primis in faucibus orci luctus et ultrices posuere cubilia curae.</p>
    </div>
    <p class="post-foot">Sed tristique purus vel augue dapibus, quis fringilla lorem bibendum. Etiam vitae ligula nec urna suscipit faucibus. Nullam vel dui ac tellus vestibulum tempor eget in mauris. Cras fermentum odio a quam pretium, eget placerat nisi venenatis. Phasellus ac nunc porta, interdum magna at, varius enim.</p>
    <span class="btn">READ MORE</span>
  </article>

  <article class="post">
    <div class="post-title">DUIS TINCIDUNT AUGUE PURUS<i></i></div>
    <div class="meta"><span>14.06.2013</span><span>By Admin</span><span>0 Comments</span><span>Portfolio</span></div>
    <div class="post-body">
      <div class="thumb" role="img" aria-label="Rows of paint tubes and brushes in warm yellow tones" style="background:linear-gradient(135deg,#f1d36a,#c98f3a 50%,#5a6a7a)"></div>
      <p>Interdum et malesuada fames ac ante ipsum primis in faucibus. Vivamus eget neque tempor vulputate nunc vitae sagittis. Quisque scelerisque mi quis nibh porta mattis sed eu velit. Nunc feugiat erat sed velit luctus, et pretium orci dictum. Donec commodo purus vel lectus gravida, vitae tincidunt massa luctus. Aliquam erat volutpat. Sed gravida augue non porta ultrices. Curabitur in lacus et odio vestibulum semper. Praesent quis arcu et neque porttitor varius sit amet eu enim. Mauris sed mauris ut nibh lacinia pulvinar. Nam ut lorem vel sapien dictum blandit. Integer vitae tortor a nisl cursus faucibus ac nec erat. Vestibulum ante ipsum primis in faucibus orci luctus et ultrices posuere cubilia curae.</p>
    </div>
    <p class="post-foot">Sed tristique purus vel augue dapibus, quis fringilla lorem bibendum. Etiam vitae ligula nec urna suscipit faucibus. Nullam vel dui ac tellus vestibulum tempor eget in mauris. Cras fermentum odio a quam pretium, eget placerat nisi venenatis. Phasellus ac nunc porta, interdum magna at, varius enim.</p>
    <span class="btn">READ MORE</span>
  </article>
</main>

<aside class="sidebar">
  <section class="widget signup">
    <h4>SIGNUP<br>FOR NEWSLETTER</h4>
    <div class="field">Name</div>
    <div class="field">Email</div>
    <span class="submit">SUBMIT</span>
  </section>
  <section class="widget">
    <h3>CATEGORIES</h3>
    <ul class="cats"><li>Design</li><li>Artist</li><li style="color:var(--orange)">Photography</li><li>Fashion</li><li>People</li><li>Style</li></ul>
  </section>
  <section class="widget">
    <h3>POPULAR POSTS</h3>
    <div class="pop"><div role="img" aria-label="Painting thumbnail" style="background:#c77a8e"></div><p>Sed ut perspiciatis unde omnis iste natus<br>14.06.2013</p></div>
    <div class="pop"><div role="img" aria-label="Painting thumbnail" style="background:#7f9ab0"></div><p>Sed ut perspiciatis unde omnis iste natus<br>14.06.2013</p></div>
    <div class="pop"><div role="img" aria-label="Painting thumbnail" style="background:#d4a25c"></div><p>Sed ut perspiciatis unde omnis iste natus<br>14.06.2013</p></div>
    <div class="pop"><div role="img" aria-label="Painting thumbnail" style="background:#8a6f5a"></div><p>Sed ut perspiciatis unde omnis iste natus<br>14.06.2013</p></div>
  </section>
  <section class="widget">
    <h3>FLICKR</h3>
    <div class="flickr">
      <div role="img" aria-label="Gallery photo" style="background:#b58b6a"></div>
      <div role="img" aria-label="Gallery photo" style="background:#6f8ba3"></div>
      <div role="img" aria-label="Gallery photo" style="background:#d77a6a"></div>
      <div role="img" aria-label="Gallery photo" style="background:#9aa37a"></div>
      <div role="img" aria-label="Gallery photo" style="background:#e0b56a"></div>
      <div role="img" aria-label="Gallery photo" style="background:#7a6a8a"></div>
    </div>
  </section>
  <section class="widget">
    <h3>TWITTER</h3>
    <div class="tweet"><i></i><p><b>@pimpim</b> Lorem ipsum dolor sit amet consectetur adipiscing elit<br>2 hours ago</p></div>
    <div class="tweet"><i></i><p><b>@pimpim</b> Lorem ipsum dolor sit amet consectetur adipiscing elit<br>2 hours ago</p></div>
    <div class="tweet"><i></i><p><b>@pimpim</b> Lorem ipsum dolor sit amet consectetur adipiscing elit<br>2 hours ago</p></div>
  </section>
</aside>

<nav class="footer-nav"><span>Home</span><span>About Us</span><span>Gallery</span><span>Latest Blog</span><span>Testimonials</span><span>Contact Us</span></nav>
<footer class="footer-bar"><span>© 2013 Pim Pim Nook. All rights reserved.</span><div class="social"><i></i><i></i><i></i></div></footer>
</body>
</html>
```